TEBSIRK HOA Portal Site for Public

Clean up and organize current website; need website to look good and functional; this is a HOA (homeowner association management) website where homeowners can login and pay their bill, general information about a HOA, monthly newsletter page.
Competitors:
https://quillmarsh.example/
https://dorvinpalms.example/
https://www.kelbrookhomes.example/nevada
http://www.tpw-hoa.example/

Target Market(s)

homeowners

Industry/Entity Type

Real Estate

Coding

Coded - Design and coding required

Number of Pages Required

5+ page

Font styles to use
Serif

Colors
0292cd
33a6d7
e667a6
e34297

Requirements
Must have
• login to pay
• services page
• contact us
• order resale package
Nice to have
• page why an HOA would contract us

```html
<!DOCTYPE html>
<html lang="en">
<head>
<meta charset="utf-8">
<title>TEBSIRK HOA</title>
<link href="https://fonts.googleapis.com/css2?family=Merriweather:wght@400;700&family=Raleway:wght@800&family=Mulish:ital,wght@0,400;0,600;1,400&display=swap" rel="stylesheet">
<style>
:root{
  --blue:#0292cd;
  --blue-soft:#33a6d7;
  --band:#2ea3d8;
  --pink:#e34297;
  --pink-soft:#e667a6;
  --ink:#222;
  --muted:#666;
  --black:#000;
  --white:#fff;
}
*{box-sizing:border-box;margin:0;padding:0}
html,body{width:1200px;height:2693px;overflow:hidden}
body{position:relative;background:var(--white);font-family:'Mulish',sans-serif;color:var(--ink)}
.abs{position:absolute}
.serif{font-family:'Merriweather',serif}
.btn{position:absolute;display:flex;align-items:center;justify-content:center;background:var(--pink);color:var(--white);font-family:'Merriweather',serif;font-weight:700;font-size:17px;border-radius:28px;text-transform:uppercase}

/* header */
.site-header{position:absolute;left:0;top:0;width:1200px;height:83px;background:var(--white)}
.brand{position:absolute;left:80px;top:26px;font-family:'Merriweather',serif;font-size:26px;color:var(--blue-soft)}
.nav{position:absolute;top:34px;display:flex;font-family:'Merriweather',serif;font-size:14.5px;color:var(--ink)}
.nav span{margin-right:22px;white-space:nowrap}
.nav .active{color:var(--pink);border-bottom:2px solid var(--pink);padding-bottom:3px}
.header-login{position:absolute;left:1070px;top:0;width:130px;height:83px;background:var(--pink);color:var(--white);display:flex;align-items:center;justify-content:center;gap:8px;font-family:'Merriweather',serif;font-size:17px}

/* hero */
.hero{position:absolute;left:0;top:83px;width:1200px;height:594px;background:linear-gradient(180deg,#3a3a36 0%,#2f332c 50%,#26281f 100%)}
.hero-title{position:absolute;left:0;width:1200px;top:180px;text-align:center;font-family:'Raleway',sans-serif;font-weight:800;font-size:47px;line-height:54px;color:var(--white)}
.hero-sub{position:absolute;left:0;width:1200px;top:300px;text-align:center;font-size:16px;color:var(--white)}
.pay-bar{position:absolute;left:77px;top:633px;width:1046px;height:92px;background:var(--band);border-radius:3px}
.pay-bar p{position:absolute;left:203px;top:30px;font-family:'Merriweather',serif;font-size:23px;color:var(--white)}

/* feature cards */
.card-img{position:absolute;top:777px;height:229px}
.card-title{position:absolute;top:1032px;font-family:'Merriweather',serif;font-weight:700;font-size:24px;color:var(--blue-soft)}
.card-text{position:absolute;top:1076px;width:325px;font-size:14.5px;line-height:27px;color:var(--muted)}

/* offer */
.offer{position:absolute;left:0;top:1318px;width:1200px;height:494px;background:var(--band)}
.offer h2{position:absolute;left:642px;top:62px;font-family:'Merriweather',serif;font-weight:400;font-size:38px;color:var(--white)}
.offer ul{position:absolute;left:648px;top:126px;list-style:none;color:var(--white);font-size:14.5px}
.offer li{height:31px}
.offer p{position:absolute;left:649px;top:261px;width:470px;font-size:14.5px;line-height:26px;color:var(--white)}

/* testimonial */
.testimonial h2{position:absolute;left:0;width:1200px;top:1868px;text-align:center;font-family:'Merriweather',serif;font-weight:700;font-size:42px;color:var(--blue)}
.quote{position:absolute;left:270px;width:660px;top:2071px;text-align:center;font-style:italic;font-size:15px;line-height:29.5px;color:#444}
.client{position:absolute;left:0;width:1200px;top:2181px;text-align:center;font-family:'Merriweather',serif;font-size:16px;color:var(--pink)}

/* footer */
.footer{position:absolute;left:0;top:2318px;width:711px;height:375px;background:var(--black)}
.footer h4{position:absolute;top:38px;font-family:'Merriweather',serif;font-weight:400;font-size:18px;color:var(--blue-soft)}
.sitemap{position:absolute;left:80px;top:88px;list-style:none;color:#ddd;font-size:14.5px}
.sitemap li{height:36.5px;display:flex;gap:14px;align-items:flex-start}
.sitemap li::before{content:"";width:5px;height:5px;border-radius:50%;background:var(--pink);margin-top:7px}
.contact-row{position:absolute;left:362px;display:flex;gap:22px;color:#ddd;font-size:14.5px;line-height:25px}
.contact-row svg{flex:none;margin-top:4px}
.socials{position:absolute;left:362px;top:2546px;display:flex;gap:6px}
.socials span{width:40px;height:40px;border-radius:50%;background:#333}
.socials span:first-child{background:var(--pink)}
.footer-rule{position:absolute;left:0;top:2623px;width:711px;height:1px;background:#222}
.copyright{position:absolute;left:80px;top:2653px;font-size:14px;color:#ccc}
.newsletter{position:absolute;left:711px;top:2318px;width:489px;height:375px;background:var(--band)}
.newsletter h3{position:absolute;left:65px;top:36px;font-family:'Merriweather',serif;font-weight:400;font-size:37px;line-height:47px;color:var(--white)}
.newsletter p{position:absolute;left:67px;top:138px;width:360px;font-size:15px;line-height:27px;color:var(--white)}
.email-field{position:absolute;left:68px;top:212px;width:344px;height:52px;background:var(--white);padding:16px 22px;font-size:14px;color:#666}
</style>
</head>
<body>

<header class="site-header">
  <div class="brand">TEBSIRK HOA</div>
  <nav class="nav" style="left:364px">
    <span class="active">HOME</span>
    <span>SERVICES</span>
    <span>ORDER RESALE PACKAGE</span>
    <span>WHY HOA CONTRACT US</span>
    <span>CONTACT US</span>
  </nav>
  <div class="header-login">
    <svg width="14" height="15" viewBox="0 0 14 15"><circle cx="7" cy="4" r="3.5" fill="#fff"/><path d="M0 15c0-5 3-7 7-7s7 2 7 7z" fill="#fff"/></svg>
    LOGIN
  </div>
</header>

<section class="hero" role="img" aria-label="Photo of a stone house entrance with steps and a leafy pathway at dusk">
  <h1 class="hero-title">HOMEOWNER ASSOCIATION<br>MANAGEMENT</h1>
  <p class="hero-sub">Lorem Ipsum is simply dummy text of the printing and typesetting.</p>
  <div class="btn" style="left:511px;top:340px;width:177px;height:52px">CONTACT US</div>
  <svg class="abs" style="left:30px;top:272px" width="20" height="46" viewBox="0 0 20 46"><path d="M18 2 2 23l16 21" fill="none" stroke="#fff" stroke-width="1.5"/></svg>
  <svg class="abs" style="left:1154px;top:272px" width="20" height="46" viewBox="0 0 20 46"><path d="M2 2l16 21L2 44" fill="none" stroke="#fff" stroke-width="1.5"/></svg>
</section>

<div class="pay-bar">
  <p>Login To Pay Your Bill With TEBSIRK HOA</p>
  <div class="btn" style="left:728px;top:23px;width:115px;height:46px;font-size:16px">LOGIN</div>
</div>

<div class="card-img" style="left:77px;width:323px;background:linear-gradient(135deg,#c8c4bc,#8a8680)" role="img" aria-label="Photo of a hand holding a small model house"></div>
<div class="card-img" style="left:433px;width:334px;background:linear-gradient(135deg,#f2f3f4,#c9ccd0)" role="img" aria-label="Photo of two colleagues working at a laptop"></div>
<div class="card-img" style="left:790px;width:333px;background:linear-gradient(135deg,#d9dde4,#3b4356)" role="img" aria-label="Photo of a hand signing a document"></div>

<h3 class="card-title" style="left:79px">About Tebsirk Hoa</h3>
<h3 class="card-title" style="left:433px">Our Services</h3>
<h3 class="card-title" style="left:790px">Why HOA Contract Us</h3>

<p class="card-text" style="left:79px">Lorem Ipsum is simply dummy text of the prin printing and typesetting industry Ipsum has is been the industry's standard dummy text ever since unknown printer.</p>
<p class="card-text" style="left:437px">Lorem Ipsum is simply dummy text of the prin printing and typesetting industry Ipsum has is been the industry's standard dummy text ever since unknown printer.</p>
<p class="card-text" style="left:794px">Lorem Ipsum is simply dummy text of the prin printing and typesetting industry Ipsum has is been the industry's standard dummy text ever since unknown printer.</p>

<div class="btn" style="left:77px;top:1202px;width:177px;height:51px">LEARN MORE</div>
<div class="btn" style="left:437px;top:1202px;width:177px;height:51px">LEARN MORE</div>
<div class="btn" style="left:795px;top:1202px;width:177px;height:51px">LEARN MORE</div>

<section class="offer">
  <div class="abs" style="left:98px;top:0;width:468px;height:494px;background:linear-gradient(180deg,#6f8a5a 0%,#9a5544 40%,#5a5a58 100%)" role="img" aria-label="Photo of a family standing in front of a brick house"></div>
  <h2>What We Offer</h2>
  <ul>
    <li>Accessible, licensed Association Managers</li>
    <li>24 hour Web site access: online account information</li>
    <li>24 hour emergency service</li>
    <li>Provide monthly financial reports to the Board of Directors</li>
  </ul>
  <p>Read, study and understand all governing documents of the Association. Correspond with members in violation of the CC&amp;Rs, By-laws, Rules &amp; Regulations and report the status of all noncompliance to the Board of Directors in a timely manner.</p>
  <div class="btn" style="left:649px;top:379px;width:177px;height:51px">LEARN MORE</div>
</section>

<section class="testimonial">
  <div class="abs" style="left:160px;top:1822px;width:880px;height:490px;background:radial-gradient(ellipse at center,#f3f4f6 0%,#fff 70%)" role="img" aria-label="Faint dotted world map backdrop"></div>
  <h2>What Our Client Say About US</h2>
  <div class="abs" style="left:550px;top:1949px;width:100px;height:100px;border-radius:50%;background:linear-gradient(160deg,#b8c4d0,#3a4658)" role="img" aria-label="Client portrait"></div>
  <p class="quote">Lorem Ipsum is simply dummy text of the prin printing and typesetting industry Ipsum has is been the industry's standard dummy text ever since unknown printer Lorem Ipsum is simply dummy text of the prin printing.</p>
  <p class="client">— &nbsp;Client Name</p>
  <svg class="abs" style="left:582px;top:2224px" width="36" height="24" viewBox="0 0 36 24"><path d="M13 2 3 12l10 10M23 2l10 10-10 10" fill="none" stroke="#111" stroke-width="2"/></svg>
</section>

<footer class="footer">
  <h4 style="left:80px">SITEMAP</h4>
  <ul class="sitemap">
    <li>Home</li><li>Services</li><li>Order Resale Package</li><li>Why HOA Contract Us</li><li>Contact Us</li>
  </ul>
  <h4 style="left:362px">CONTACT US</h4>
</footer>
<div class="contact-row" style="top:2393px">
  <svg width="18" height="24" viewBox="0 0 18 24"><path d="M9 0a9 9 0 0 0-9 9c0 7 9 15 9 15s9-8 9-15a9 9 0 0 0-9-9z" fill="#e34297"/><circle cx="9" cy="9" r="3.5" fill="#000"/></svg>
  <span>101 - Address city location, Area,<br>Pincode, Zip...</span>
</div>
<div class="contact-row" style="top:2457px">
  <svg width="20" height="18" viewBox="0 0 20 18"><path d="M4 1l3 4-2 2c1 3 4 6 7 7l2-2 4 3-2 3C8 18 1 11 1 3z" fill="#e34297"/></svg>
  <span>123 456 7890</span>
</div>
<div class="contact-row" style="top:2501px">
  <svg width="20" height="16" viewBox="0 0 20 16"><rect width="20" height="16" rx="2" fill="#e34297"/><path d="M1 2l9 7 9-7" fill="none" stroke="#000" stroke-width="1.6"/></svg>
  <span>info@TebsirkHOA.example</span>
</div>
<div class="socials" aria-label="Social profile links"><span></span><span></span><span></span><span></span></div>
<div class="footer-rule"></div>
<p class="copyright">©TEBSIRK HOA - 2019 All rights reserved.</p>

<aside class="newsletter">
  <h3>Newsletter<br>Subscription</h3>
  <p>Would you like to Receive our Exclusive News and update for sign up Our Newsletter !</p>
  <div class="email-field">Enter Email *</div>
  <div class="btn" style="left:69px;top:273px;width:167px;height:52px;border-radius:0;font-size:18px">SUBSCRIBE</div>
</aside>

</body>
</html>
```